Awesome photographers card for an awesome new business

Double sided business card Black background and silver logo in middle on one side. Details on otherside. please keep it simple

Industry/Entity Type

Photographer

Contact Information for Business Card

Gerald Fenwick
0452817360
GeraldFenwickPhotography47@mailbox.test
www.GeraldFenwickPhotography.test.au
Instagram _Gerald_fenwick

Requirements
Must have
• My logo in Silver
• please use instagram logo instead of "Instagram"

```html
<!DOCTYPE html>
<html lang="en">
<head>
<meta charset="utf-8">
<title>Gerald Fenwick Photography – Business Card</title>
<link href="https://fonts.googleapis.com/css2?family=Roboto:wght@400;500&family=Roboto+Condensed:wght@500&display=swap" rel="stylesheet">
<style>
  :root {
    --backdrop: #2a2b2d;
    --card: #1d1e20;
    --card-edge: #161718;
    --silver-light: #f1f1f1;
    --silver-mid: #c9c9c9;
    --silver-dark: #a9a9a9;
    --band-text: #4f5052;
    --logo-silver: #cfcfcf;
    --url-text: #e8e8e8;
  }
  * { margin: 0; padding: 0; box-sizing: border-box; }
  html, body {
    width: 1200px; height: 960px; overflow: hidden;
    background: var(--backdrop);
    font-family: "Roboto", Arial, sans-serif;
  }
  .canvas { position: relative; width: 1200px; height: 960px; }

  .card {
    position: absolute;
    width: 600px; height: 342px;
    background: var(--card);
    box-shadow: 0 4px 10px rgba(0,0,0,.45);
    overflow: hidden;
  }
  .card--front { left: 314px; top: 113px; }
  .card--back { left: 312px; top: 473px; height: 340px; }

  .brand-mark {
    position: absolute; left: 0; right: 0;
    display: flex; align-items: center; justify-content: center; gap: 12px;
  }
  .card--front .brand-mark { top: 92px; }
  .card--back .brand-mark { top: 130px; }
  .brand-mark__dot {
    width: 14px; height: 14px; border-radius: 50%;
    background: var(--logo-silver);
  }
  .brand-mark__name {
    font-family: "Roboto", Arial, sans-serif;
    font-weight: 400;
    font-size: 26px;
    letter-spacing: 4px;
    color: var(--logo-silver);
    text-transform: uppercase;
  }

  .details-band {
    position: absolute; left: 0; top: 211px;
    width: 100%; height: 108px;
    background: linear-gradient(90deg, var(--silver-dark) 0%, var(--silver-light) 45%, var(--silver-mid) 100%);
    text-align: center;
    color: var(--band-text);
  }
  .details-band__name {
    margin-top: 18px;
    font-family: "Roboto Condensed", Arial, sans-serif;
    font-weight: 500;
    font-size: 21px;
    letter-spacing: .3px;
  }
  .details-band__row {
    display: flex; justify-content: center; align-items: center; gap: 6px;
    font-size: 14.5px; line-height: 20px;
  }
  .details-band__row:first-of-type { margin-top: 8px; }
  .contact-item { display: inline-flex; align-items: center; gap: 3px; }
  .contact-item svg { width: 12px; height: 12px; fill: var(--band-text); }

  .card-url {
    position: absolute; left: 0; right: 0; top: 290px;
    text-align: center;
    font-size: 15px; letter-spacing: 2.2px;
    color: var(--url-text);
  }
</style>
</head>
<body>
<main class="canvas">

  <section class="card card--front" aria-label="Card front">
    <div class="brand-mark">
      <span class="brand-mark__dot"></span>
      <span class="brand-mark__name">Gerald Fenwick</span>
    </div>

    <div class="details-band">
      <h1 class="details-band__name">GERALD FENWICK</h1>
      <p class="details-band__row">
        <span class="contact-item">
          <svg viewBox="0 0 24 24" aria-hidden="true"><path d="M6.6 10.8c1.4 2.8 3.8 5.1 6.6 6.6l2.2-2.2c.3-.3.7-.4 1-.2 1.1.4 2.3.6 3.6.6.6 0 1 .4 1 1V20c0 .6-.4 1-1 1C10.6 21 3 13.4 3 4c0-.6.4-1 1-1h3.5c.6 0 1 .4 1 1 0 1.3.2 2.5.6 3.6.1.3 0 .7-.2 1z"/></svg>
          0452817360
        </span>
        <span class="contact-item">
          <svg viewBox="0 0 24 24" aria-hidden="true"><path d="M2 5h20v14H2z M2 5l10 8 10-8" /><path d="M3 6l9 7 9-7V5H3z" fill="#e6e6e6"/></svg>
          GeraldFenwickPhotography47@mailbox.test
        </span>
      </p>
      <p class="details-band__row">
        <span class="contact-item">
          <svg viewBox="0 0 24 24" aria-hidden="true"><circle cx="12" cy="12" r="10"/></svg>
          www.GeraldFenwickPhotography.test.au
        </span>
        <span class="contact-item">
          <svg viewBox="0 0 24 24" aria-hidden="true"><rect x="2" y="2" width="20" height="20" rx="3"/></svg>
          Gerald_fenwick
        </span>
      </p>
    </div>
  </section>

  <section class="card card--back" aria-label="Card back">
    <div class="brand-mark">
      <span class="brand-mark__dot"></span>
      <span class="brand-mark__name">Gerald Fenwick</span>
    </div>
    <p class="card-url">www.GeraldFenwickPhotography.test.au</p>
  </section>

</main>
</body>
</html>
```